Copper Field Agency Website - Wordpress Web UPDATED BRIEF

FINAL LOGO UPLOADED - please look to this as reference for how we would like the site to look and feel.

We are a digital marketing agency - looking to have a new website built. We are looking for a simple one page feel of site that will allow us to grow it later. (Feel free to take some liberties with that if your imagination veers off) Must be very, playful, bold, sleek and easily integrate video. Wordpress only.

Overview:

Copper Field is a creative constellation. We are built on what's great about the shared economy. With access to thousands of content creators, designers, technicians, writers, strategists and other creatives around the world, we are built differently than a traditional “brick and mortar” Marketing Agency. We provide the traditional services our clients have come to expect, without the “5X factor” of covering the overhead common in the old agency model. We believe even better work can be created in collaboration with our clients and by passing those savings back to them for their use. Our clients pay for our art, our work and our passion –not our furniture.

"Copper Field, Let's Build Together"

Target Market(s)

companies looking for creative agency help, video production, creative consulting and coaching

Industry/Entity Type

Digital Marketing

Coding

Coded - Design and coding required

Number of Pages Required

1 page

Font styles to use
Sans Serif

Colors
3277b5
33a6d7
ec1f27

Requirements
Must have
• Wordpress design is a must. Looking for a one sheet homepage - with sections that are all on the main front page. We will have videos to embed, and should be able to have client logos and easy access to show a variety of our creative work.
• Please look to the logo for how we would like the site to feel.
• Please think "icon process flow" instead of blocks of text (which we used to have). Use the text to explain what the process flow should represent - don't actually copy paste the text but show it visually in icons.
Nice to have
• innovation around how we show video content. solid colors complementary to our palette and aesthetic.
Should not have
• Standard HTML coding

```html
<!DOCTYPE html>
<html lang="en">
<head>
<meta charset="utf-8">
<title>Copper Field Agency</title>
<link href="https://fonts.googleapis.com/css2?family=Oswald:wght@300;400;500;600&family=Open+Sans:wght@400;600;700&display=swap" rel="stylesheet">
<style>
:root{
  --blue:#3277b5;
  --sky:#33a6d7;
  --red:#ec1f27;
  --red-deep:#d91a2a;
  --ink:#2b2f36;
  --muted:#6b7078;
  --line:#e3e7ee;
  --white:#ffffff;
  --pale:#eef5fb;
}
*{margin:0;padding:0;box-sizing:border-box}
html,body{width:1200px;height:4360px;overflow:hidden}
body{font-family:"Open Sans",Arial,sans-serif;color:var(--ink);background:var(--white);position:relative}
.heading{font-family:"Oswald",Arial,sans-serif;font-weight:400;text-transform:uppercase;font-size:40px;letter-spacing:1px;text-align:center;color:var(--blue)}
.heading span{color:var(--red)}

/* header */
.site-header{position:absolute;top:0;left:0;width:1200px;height:110px;background:var(--white);z-index:3;box-shadow:0 2px 10px rgba(0,0,0,.08)}
.brand{position:absolute;left:80px;top:8px;display:flex;align-items:center;gap:12px;background:var(--white);border-radius:60px;padding:10px 22px 10px 10px}
.brand-dot{width:90px;height:90px;border-radius:50%;background:var(--blue)}
.brand-name{font-family:"Oswald",Arial,sans-serif;font-weight:600;font-size:26px;color:var(--blue);text-transform:uppercase;line-height:1}
.main-nav{position:absolute;right:110px;top:44px;display:flex;gap:34px}
.main-nav a{font-family:"Oswald",Arial,sans-serif;font-size:15px;color:var(--ink);text-decoration:none;text-transform:uppercase;letter-spacing:.5px}
.main-nav a.active{color:var(--red)}

/* hero */
.hero{position:absolute;top:110px;left:0;width:1200px;height:690px;overflow:hidden}
.hero-photo{position:absolute;inset:0;background:linear-gradient(110deg,#3a3530 0%,#6a5a4e 35%,#2d3440 70%,#1d222b 100%)}
.hero-caption{position:absolute;left:110px;top:210px;width:420px;padding:28px 30px;background:rgba(20,24,30,.55)}
.hero-caption h1{font-family:"Oswald",Arial,sans-serif;font-weight:400;font-size:40px;color:var(--white)}
.hero-caption p{font-size:22px;line-height:1.35;color:var(--white);margin:12px 0 22px}
.btn{display:inline-block;font-family:"Oswald",Arial,sans-serif;font-size:16px;color:var(--white);text-decoration:none;padding:10px 26px;border-radius:30px;text-transform:uppercase}
.btn-blue{background:var(--blue);text-transform:none;font-family:"Open Sans",Arial,sans-serif}
.btn-red{background:var(--red)}
.arrow{position:absolute;top:330px;width:34px;height:34px;border-radius:50%;background:rgba(255,255,255,.85);display:flex;align-items:center;justify-content:center}
.arrow.prev{left:56px}.arrow.next{right:56px}
.hero-wave{position:absolute;left:0;bottom:0;width:1200px;height:120px}

/* welcome + clients background */
.soft-band{position:absolute;top:800px;left:0;width:1200px;height:1100px;background:linear-gradient(180deg,#ffffff 0%,var(--pale) 30%,#ffffff 60%,var(--pale) 85%,#ffffff 100%)}
.welcome{position:absolute;top:890px;left:112px;width:976px;display:flex;gap:50px}
.video-thumb{position:relative;width:570px;height:280px;background:linear-gradient(135deg,#505866,#8a8e96 45%,#3a4350)}
.play{position:absolute;left:50%;top:50%;width:70px;height:70px;margin:-35px 0 0 -35px;border-radius:50%;border:3px solid var(--white);display:flex;align-items:center;justify-content:center}
.welcome-text{width:356px;padding-top:20px}
.welcome-text h2{font-family:"Oswald",Arial,sans-serif;font-weight:400;font-size:32px;color:var(--blue);text-transform:uppercase}
.welcome-text h2 span{color:var(--red)}
.welcome-text p{font-size:12.5px;line-height:1.7;color:var(--muted);margin:14px 0 22px}

.clients{position:absolute;top:1390px;left:0;width:1200px}
.client-row{display:flex;justify-content:center;gap:128px;margin-top:56px}
.client-row+.client-row{margin-top:36px}
.client{width:118px;height:118px;border-radius:50%;background:var(--white);box-shadow:0 4px 16px rgba(50,119,181,.18);display:flex;align-items:center;justify-content:center;font-size:15px;font-weight:600;color:#8a9099}
.client.featured{box-shadow:0 0 0 2px rgba(236,31,39,.35),0 4px 16px rgba(236,31,39,.2)}

/* gallery */
.gallery{position:absolute;top:1930px;left:0;width:1200px;height:560px}
.tile{position:absolute}
.t1{left:112px;top:90px;width:480px;height:220px;background:linear-gradient(135deg,var(--blue),#1d4e86 60%,#c7424a)}
.t2{left:600px;top:90px;width:240px;height:448px;background:linear-gradient(180deg,#8c7c6c,#5a4a40 60%,#3f4a3a)}
.t3{left:848px;top:90px;width:240px;height:220px;background:linear-gradient(135deg,#6c5a48,#a38a70 50%,#3c3a38)}
.t4{left:112px;top:318px;width:232px;height:220px;background:linear-gradient(135deg,#102a4a,#2d6aa8 50%,#e2733a)}
.t5{left:352px;top:318px;width:240px;height:220px;background:linear-gradient(135deg,#7a6a58,#c7b49a 50%,#4a4440)}
.t6{left:848px;top:318px;width:240px;height:220px;background:linear-gradient(135deg,#4a5a40,#8a8a6a 50%,#3a3530)}
.zoom{position:absolute;left:50%;top:50%;width:60px;height:60px;margin:-30px 0 0 -30px;border-radius:50%;border:2px solid var(--white);display:flex;align-items:center;justify-content:center}

/* services */
.services{position:absolute;top:2520px;left:0;width:1200px;height:590px;background:linear-gradient(180deg,var(--red),var(--red-deep))}
.services .heading{color:var(--white);margin-top:44px}
.service-grid{display:grid;grid-template-columns:repeat(3,340px);justify-content:center;row-gap:36px;margin-top:38px}
.service{text-align:center;color:var(--white)}
.service svg{width:62px;height:62px}
.service h3{font-family:"Oswald",Arial,sans-serif;font-weight:400;font-size:17px;text-transform:uppercase;margin-top:12px}
.btn-outline{display:block;width:190px;margin:40px auto 0;text-align:center;border:2px solid var(--white);border-radius:30px;color:var(--white);font-family:"Oswald",Arial,sans-serif;font-size:16px;padding:8px 0;text-decoration:none;text-transform:uppercase}

/* testimonials */
.testimonials{position:absolute;top:3140px;left:0;width:1200px;height:480px}
.quotes{display:flex;justify-content:center;gap:120px;margin-top:40px}
.quote{width:400px;text-align:center}
.avatar{width:128px;height:128px;border-radius:50%;margin:0 auto;background:radial-gradient(circle at 50% 40%,#b08e78,#5a4438 70%);border:4px solid var(--white);box-shadow:0 3px 10px rgba(0,0,0,.15)}
.quote h4{font-family:"Oswald",Arial,sans-serif;font-weight:400;font-size:15px;text-transform:uppercase;margin-top:20px;color:var(--ink)}
.stars{color:#f4b400;font-size:18px;letter-spacing:2px;margin:4px 0 12px}
.quote p{font-size:16px;line-height:1.6;color:var(--muted);position:relative;padding:0 24px}
.quote p::before{content:"\201C";position:absolute;left:0;top:-8px;font-size:40px;color:var(--ink);font-family:Georgia,serif}
.quote p::after{content:"\201D";position:absolute;right:0;bottom:-24px;font-size:40px;color:var(--ink);font-family:Georgia,serif}

/* contact */
.contact{position:absolute;top:3620px;left:0;width:1200px;height:460px;background:linear-gradient(180deg,#2f6fae,var(--blue) 50%,#2a64a2)}
.contact .heading{color:var(--white);margin-top:50px}
.contact-form{width:504px;margin:36px auto 0;display:grid;grid-template-columns:1fr 1fr;gap:10px}
.field{height:40px;border:1px solid rgba(255,255,255,.7);color:var(--white);font-size:12px;padding:11px 12px}
.field.message{grid-column:1/3;height:100px}
.submit{grid-column:1/3;justify-self:center;margin-top:20px;background:var(--red);color:var(--white);font-family:"Oswald",Arial,sans-serif;font-size:16px;text-transform:uppercase;padding:9px 40px;border-radius:30px}

/* footer */
.site-footer{position:absolute;top:4080px;left:0;width:1200px;height:280px;text-align:center}
.site-footer .brand{position:static;display:inline-flex;margin-top:28px}
.footer-nav{display:flex;justify-content:center;gap:32px;margin-top:30px}
.footer-nav a{font-family:"Oswald",Arial,sans-serif;font-size:13px;color:var(--ink);text-decoration:none;text-transform:uppercase}
.footer-nav a.active{color:var(--red)}
.copyright{font-size:12px;color:var(--muted);margin-top:14px;text-transform:uppercase}
</style>
</head>
<body>

<header class="site-header">
  <div class="brand"><div class="brand-dot"></div><div class="brand-name">Copper Field</div></div>
  <nav class="main-nav">
    <a class="active" href="#">Home</a><a href="#">Video</a><a href="#">Clients Logo</a><a href="#">Our Work</a><a href="#">Services</a><a href="#">Testimonials</a><a href="#">Contact</a>
  </nav>
</header>

<section class="hero">
  <div class="hero-photo" role="img" aria-label="Photo of a creative team working together on laptops in a brick-walled office"></div>
  <div class="hero-caption">
    <h1>Copper Field</h1>
    <p>Sed ut perspiciatis unde omnis iste nat us error sit voluptatem</p>
    <a class="btn btn-blue" href="#">Read More</a>
  </div>
  <div class="arrow prev"><svg width="14" height="14" viewBox="0 0 14 14"><path d="M9 2L4 7l5 5" fill="none" stroke="#2b2f36" stroke-width="2"/></svg></div>
  <div class="arrow next"><svg width="14" height="14" viewBox="0 0 14 14"><path d="M5 2l5 5-5 5" fill="none" stroke="#2b2f36" stroke-width="2"/></svg></div>
  <svg class="hero-wave" viewBox="0 0 1200 120" preserveAspectRatio="none">
    <path d="M0 70 C200 20 400 110 600 70 S1000 20 1200 60 V120 H0Z" fill="#ffffff"/>
    <path d="M0 60 C200 10 400 100 600 60 S1000 10 1200 50" fill="none" stroke="#3277b5" stroke-width="4"/>
    <path d="M0 80 C220 40 420 120 620 82 S1000 40 1200 72" fill="none" stroke="#33a6d7" stroke-width="2"/>
  </svg>
</section>

<div class="soft-band"></div>

<section class="welcome">
  <div class="video-thumb" role="img" aria-label="Video still of colleagues talking in a bright office">
    <div class="play"><svg width="26" height="26" viewBox="0 0 26 26"><path d="M8 4l14 9-14 9z" fill="#fff"/></svg></div>
  </div>
  <div class="welcome-text">
    <h2>Welcome to <span>Copper</span></h2>
    <p>Copper Field is a creative constellation. We are built on what's great about the shared economy. With access to thousands of content creators, designers, technicians, writers, strategists and other creatives around the world, we are built differently than a traditional "brick and mortar" Marketing Agency. We provide the traditional services our clients expect, without the overhead of the old agency model.</p>
    <a class="btn btn-red" href="#">Watch Video</a>
  </div>
</section>

<section class="clients">
  <h2 class="heading">Our <span>Clients</span></h2>
  <div class="client-row">
    <div class="client">Nordell</div><div class="client featured">Omera</div><div class="client">Brightwave</div><div class="client">Halvora</div>
  </div>
  <div class="client-row">
    <div class="client">Sintok</div><div class="client">Fernglade</div><div class="client">Cloverhaus</div>
  </div>
</section>

<section class="gallery">
  <h2 class="heading" style="color:var(--red)"><span style="color:var(--red)">Photo</span> Gallery</h2>
  <div class="tile t1" role="img" aria-label="Blue digital technology image"><div class="zoom"><svg width="24" height="24" viewBox="0 0 24 24"><path d="M12 3v18M3 12h18" stroke="#fff" stroke-width="2"/></svg></div></div>
  <div class="tile t2" role="img" aria-label="Portrait of a smiling businesswoman"></div>
  <div class="tile t3" role="img" aria-label="Team meeting around a laptop"></div>
  <div class="tile t4" role="img" aria-label="Colourful digital interface close-up"></div>
  <div class="tile t5" role="img" aria-label="Designers working at a desk"></div>
  <div class="tile t6" role="img" aria-label="Group collaborating at a table"></div>
</section>

<section class="services">
  <h2 class="heading">Our Services</h2>
  <div class="service-grid">
    <div class="service"><svg viewBox="0 0 62 62" fill="none" stroke="#fff" stroke-width="2.5"><circle cx="31" cy="31" r="26"/><path d="M40 22l-6 12-12 6 6-12z"/></svg><h3>Discovery</h3></div>
    <div class="service"><svg viewBox="0 0 62 62" fill="none" stroke="#fff" stroke-width="2.5"><rect x="8" y="8" width="46" height="34"/><path d="M31 42v12M20 54h22M14 34l10-10 8 6 14-14"/></svg><h3>Strategy</h3></div>
    <div class="service"><svg viewBox="0 0 62 62" fill="none" stroke="#fff" stroke-width="2.5"><circle cx="31" cy="12" r="6"/><circle cx="12" cy="48" r="6"/><circle cx="31" cy="48" r="6"/><circle cx="50" cy="48" r="6"/><path d="M31 18v12M12 42v-8h38v8M31 30v12"/></svg><h3>Project Management</h3></div>
    <div class="service"><svg viewBox="0 0 62 62" fill="none" stroke="#fff" stroke-width="2.5"><path d="M14 6h24l10 10v40H14z"/><path d="M38 6v10h10M20 26h22M20 34h22M20 42h16"/></svg><h3>Content</h3></div>
    <div class="service"><svg viewBox="0 0 62 62" fill="none" stroke="#fff" stroke-width="2.5"><circle cx="31" cy="31" r="9"/><path d="M31 6v8M31 48v8M6 31h8M48 31h8M13 13l6 6M43 43l6 6M13 49l6-6M43 19l6-6"/><circle cx="31" cy="31" r="18"/></svg><h3>Production</h3></div>
    <div class="service"><svg viewBox="0 0 62 62" fill="none" stroke="#fff" stroke-width="2.5"><rect x="6" y="6" width="50" height="50" rx="6"/><path d="M18 44V28h6l6-12c4 0 4 4 3 8h10c3 0 4 3 3 5l-3 12c-1 2-2 3-4 3z"/></svg><h3>Paid Media</h3></div>
  </div>
  <a class="btn-outline" href="#">View More</a>
</section>

<section class="testimonials">
  <h2 class="heading" style="color:var(--red)"><span>Our</span> <span style="color:var(--blue)">Testimonials</span></h2>
  <div class="quotes">
    <div class="quote">
      <div class="avatar" role="img" aria-label="Client portrait"></div>
      <h4>Marla Quinn / Northside Studio</h4>
      <div class="stars">★★★★★</div>
      <p>Copper Field is proving to be force in the creative consulting industry and we look forward to collaborating with them again in the future</p>
    </div>
    <div class="quote">
      <div class="avatar" role="img" aria-label="Client portrait"></div>
      <h4>Harbor Arts Collective</h4>
      <div class="stars">★★★★★</div>
      <p>Copper Field has helped us to focus to develop our work, build a narrative arc and coalesce our ideas to achieve a relatable work of art</p>
    </div>
  </div>
</section>

<section class="contact">
  <h2 class="heading">Contact Us</h2>
  <div class="contact-form">
    <div class="field">First Name:</div><div class="field">Last Name:</div>
    <div class="field">Email:</div><div class="field">Phone:</div>
    <div class="field message">Message:</div>
    <div class="submit">Submit</div>
  </div>
</section>

<footer class="site-footer">
  <div class="brand"><div class="brand-dot"></div><div class="brand-name">Copper Field</div></div>
  <nav class="footer-nav">
    <a class="active" href="#">Home</a><a href="#">Video</a><a href="#">Clients Logo</a><a href="#">Our Work</a><a href="#">Services</a><a href="#">Testimonials</a><a href="#">Contact</a>
  </nav>
  <p class="copyright">© Copyrights 2019 Copper Field. All Rights Reserved.</p>
</footer>

</body>
</html>
```